KLORA product web page

We need a new web design for our KLORA product page. You can find more information about the project on the current web site - www.klora.example

What we need from a new design (uncoded):
- landing pages + template
- all information on one page
- the design should be focused on the product - light bulb + app
- web site should be with some dynamics like a background with parallax effect in the current version
- fonts should be chosen
- a number of illustrations should be designed

Here is schema for a new design: https://files.examplehost.net/d/draw-7QpX2mLk9RtYv4Hs/edit

Here is a document with all texts for a new design: https://files.examplehost.net/d/doc-3WnZ8bJf5KcUe1Ga/edit

Illustrations to use:
v1 - https://files.examplehost.net/f/fold-A1kT9pQw2ZxR
v2 - https://files.examplehost.net/f/fold-B7mH4sLv6YcN

PhoneOS screens: https://files.examplehost.net/f/fold-C3rJ8dKe1WuP

KLORA logo: https://files.examplehost.net/f/fold-D5nF2gTb9XoM
Updates

I forgot to add the definition text "KLORA - is.." to the document with texts. Sorry, my mistake.

Target Market(s)

25-45 year old adults who are interested in "smart" devices for their health.

Industry/Entity Type

Brintel

Colors

Designer to choose colors to be used in the design.

Requirements
Must have
• - landing pages + template
- fonts should be chosen

```html
<!DOCTYPE html>
<html lang="en">
<head>
<meta charset="utf-8">
<title>KLORA – Smart Lightbulb</title>
<link rel="stylesheet" href="https://fonts.googleapis.com/css2?family=Source+Sans+3:wght@400;600;700&display=swap">
<style>
  :root {
    --purple: #6a5a9c;
    --purple-dark: #4f4380;
    --grey-band: #e3e3e3;
    --teal: #4fbdd0;
    --ink: #3d3d3d;
    --muted: #6f6f6f;
    --white: #ffffff;
    --paper: #f8f8f8;
    --footer: #2f2f2f;
    --button: #2b2b2b;
  }
  * { box-sizing: border-box; margin: 0; padding: 0; }
  html, body { width: 1200px; height: 2305px; overflow: hidden; }
  body {
    font-family: "Source Sans 3", sans-serif;
    color: var(--ink);
    background: var(--white);
    position: relative;
  }
  .abs { position: absolute; }

  /* Header */
  .site-header { position: absolute; left: 0; top: 0; width: 1200px; height: 126px; background: var(--white); }
  .brand {
    position: absolute; left: 132px; top: 11px; width: 100px; height: 100px;
    border-radius: 50%; background: var(--purple);
    display: flex; align-items: center; justify-content: center;
    color: var(--white); font-weight: 700; font-size: 22px; letter-spacing: 1px;
  }
  .main-nav { position: absolute; right: 140px; top: 71px; display: flex; gap: 14px; font-size: 14px; color: var(--purple-dark); }
  .main-nav a { color: var(--purple-dark); text-decoration: none; }
  .main-nav a.current { color: var(--purple); font-weight: 600; }
  .main-nav .sep { color: var(--muted); }

  /* Hero */
  .hero { position: absolute; left: 0; top: 126px; width: 1200px; height: 668px; overflow: hidden; }
  .hero-scene {
    position: absolute; inset: 0;
    background:
      radial-gradient(ellipse 170px 320px at 925px 300px, #e8e8e8 0%, #5b5e62 55%, transparent 80%),
      linear-gradient(180deg, #7fb7d6 0%, #b9d4e2 38%, #c7a07a 62%, #b67d4f 100%);
  }
  .hero-title { position: absolute; left: 132px; top: 210px; font-size: 58px; font-weight: 700; color: var(--white); letter-spacing: -0.5px; text-transform: uppercase; }
  .hero-lead { position: absolute; left: 132px; top: 310px; width: 560px; font-size: 24px; line-height: 36px; color: #2b2f3a; text-transform: uppercase; }
  .hero-actions { position: absolute; left: 134px; top: 422px; display: flex; gap: 17px; }
  .btn {
    display: inline-block; width: 100px; height: 31px; line-height: 31px; border-radius: 16px;
    background: var(--button); color: var(--white); font-size: 12px; font-weight: 600;
    text-align: center; text-transform: uppercase; text-decoration: none;
  }
  .slider-dots { position: absolute; left: 135px; top: 503px; display: flex; gap: 4px; }
  .slider-dots span { width: 15px; height: 15px; border-radius: 50%; background: #6a6a6a; }
  .slider-dots span.active { background: #222; }

  /* Intro */
  .intro { position: absolute; left: 140px; top: 835px; width: 920px; text-align: center; font-size: 13.5px; line-height: 20px; color: var(--muted); }

  /* Feature tiles */
  .tile { position: absolute; width: 600px; height: 372px; }
  .tile h2 { position: absolute; top: 20px; font-size: 34px; font-weight: 600; }
  .tile p { position: absolute; font-size: 13.5px; line-height: 22px; }
  .tile .art { position: absolute; }
  .tile-app { left: 0; top: 958px; background: var(--purple); color: var(--white); }
  .tile-color { left: 600px; top: 958px; background: var(--grey-band); color: var(--ink); }
  .tile-health { left: 0; top: 1330px; background: var(--grey-band); color: var(--ink); }
  .tile-design { left: 600px; top: 1330px; background: var(--teal); color: var(--white); }

  .chevron {
    position: absolute; left: 580px; width: 40px; height: 40px; border-radius: 50%;
    background: var(--white); box-shadow: 0 1px 4px rgba(0,0,0,.35); z-index: 3;
    display: flex; align-items: center; justify-content: center;
  }

  /* Specs */
  .specs { position: absolute; left: 0; top: 1700px; width: 1200px; height: 484px; background: var(--paper); }
  .specs .art { position: absolute; left: 535px; top: 80px; width: 135px; height: 140px; border-radius: 20px; background: linear-gradient(135deg, #1f86c6 0%, #1f86c6 50%, #5e5e5e 50%, #5e5e5e 100%); }
  .specs h2 { position: absolute; left: 0; width: 1200px; top: 255px; text-align: center; font-size: 30px; font-weight: 600; color: var(--ink); }
  .specs p { position: absolute; left: 170px; width: 860px; top: 315px; text-align: center; font-size: 13.5px; line-height: 23px; color: var(--muted); }
  .specs .more { position: absolute; left: 0; width: 1200px; top: 425px; text-align: center; font-size: 12px; font-style: italic; color: var(--purple-dark); text-decoration: none; }

  /* Footer */
  .site-footer { position: absolute; left: 0; top: 2184px; width: 1200px; height: 121px; background: var(--footer); color: #cfcfcf; font-size: 14px; }
  .footer-nav { position: absolute; left: 123px; top: 34px; display: flex; gap: 10px; }
  .footer-nav a { color: #d8d8d8; text-decoration: none; }
  .copyright { position: absolute; left: 123px; top: 66px; }
  .social { position: absolute; left: 956px; top: 46px; display: flex; gap: 5px; }
  .social span { width: 27px; height: 27px; border-radius: 50%; background: #8a8a8a; }
</style>
</head>
<body>

<header class="site-header">
  <div class="brand">KLORA</div>
  <nav class="main-nav">
    <a class="current" href="#">PRE ORDER</a><span class="sep">/</span>
    <a href="#">BLOG</a><span class="sep">/</span>
    <a href="#">CONTACT</a><span class="sep">/</span>
    <a href="#">RU</a>
  </nav>
</header>

<section class="hero">
  <div class="hero-scene" role="img" aria-label="KLORA smart lightbulb standing on a wooden table with a soft blurred blue room behind"></div>
  <h1 class="hero-title">Turn your KLORA on!</h1>
  <p class="hero-lead">Create light scenes and adapt them to your needs with KLORA app.</p>
  <div class="hero-actions">
    <a class="btn" href="#">Pre order</a>
    <a class="btn" href="#">View more</a>
  </div>
  <div class="slider-dots"><span class="active"></span><span></span><span></span><span></span></div>
</section>

<p class="intro">Lorem ipsum dolor sit amet, consectetuer adipiscing elit, sed diam nonummy nibh euismod tincidunt laoreet dolore magna aliquam erat volutpat. Ut wisi enim ad minim veniam, quis nostrud exerci tation ullamcorper suscipit lobortis nisl ut aliquip ex ea commodo consequat. Duis autem vel eum iriure dolor in hendrerit in vulputate velit esse molestie consequat, vel illum dolore eu feugiat nulla facilisis at vero eros et accumsan et iusto odio dignissim qui blandit praesent luptatum zzril delenit augue duis dolore te feugait nulla facilisi.</p>

<div class="chevron" style="top:940px"><svg width="18" height="12" viewBox="0 0 18 12"><path d="M2 2l7 7 7-7" fill="none" stroke="#333" stroke-width="3"/></svg></div>

<section class="tile tile-app">
  <h2 style="left:132px">KLORA App</h2>
  <div class="art" role="img" aria-label="Smartphone illustration" style="left:134px;top:86px;width:76px;height:140px;border-radius:12px;background:#f4f4f4;"></div>
  <p style="left:232px;top:88px;width:340px">KLORA Application allows you to control each lightbulb at home. Manage your lighting by creating functional group and adding / excluding lightbulbs. Correctly matched lighting will help you work more productively and relax to the outmost.</p>
  <p style="left:134px;top:250px;width:440px">Create light scenes and adapt them to your needs. KLORA App memorizes your favorite moods, so that you can use your settings anytime. Play with million colors and adjust the brightness of your home lighting. KLORA works on PhoneOS 6+ and Droidline 4+.</p>
</section>

<section class="tile tile-color">
  <h2 style="left:13px">KLORA and color</h2>
  <div class="art" role="img" aria-label="Colour swatch fan illustration" style="left:15px;top:88px;width:160px;height:140px;border-radius:6px;background:linear-gradient(160deg,#e4e04a,#e8596b,#6a5a9c,#5cc45a,#4fbdd0);"></div>
  <p style="left:196px;top:88px;width:270px">Experiment with millions of colors! Pick any color from the screen of your mobile device and enjoy the ambience. LED lightbulb KLORA can transform conventional lighting into the night lights of Seattle or bring in the rich summer hues of Provence.</p>
  <p style="left:13px;top:250px;width:450px">Enliven your fantasies or raise your best memories in one click. Change the atmosphere around you by changing colors. You will literally see the world in a new light.</p>
</section>

<div class="chevron" style="top:1310px"><svg width="18" height="12" viewBox="0 0 18 12"><path d="M2 2l7 7 7-7" fill="none" stroke="#333" stroke-width="3"/></svg></div>

<section class="tile tile-health">
  <h2 style="left:132px">KLORA and health</h2>
  <div class="art" role="img" aria-label="Red heart with tick illustration" style="left:132px;top:88px;width:158px;height:140px;border-radius:14px;background:#e02127;"></div>
  <p style="left:316px;top:88px;width:270px">Choose a scene for setting the alarm and improve your sleep naturally. KLORA lighting system creates the necessary conditions for normalizing your circadian rhythms. Set your smart lightbulbs to turn on: now you can wake up "on the sunny side" despite gloomy weather. KLORA lighting system will reduce your stress level.</p>
  <p style="left:132px;top:280px;width:460px">10 preset moods provide positive impact on your health. Designed to be what your mind and body need. We developed predefined modes.</p>
</section>

<section class="tile tile-design">
  <h2 style="left:18px">Lighting Design</h2>
  <div class="art" role="img" aria-label="Award ribbon badge illustration" style="left:16px;top:88px;width:108px;height:160px;border-radius:50px 50px 8px 8px;background:#5a5a5a;"></div>
  <p style="left:150px;top:88px;width:320px">Wireless lightbulbs with LinkWave and MeshBee help you implement the concept of the smart home. KLORA makes it affordable. Real lighting design at your place, couldn't have been simpler.</p>
  <p style="left:150px;top:202px;width:320px">Create optimal lighting for each functional area - set the perfect light for your kitchen, living room and</p>
  <p style="left:18px;top:280px;width:460px">set your color mood, pick a palette for each room. Stay informed of every smart lightbulb's condition, save your settings and load them anytime.</p>
</section>

<div class="chevron" style="top:1680px"><svg width="18" height="12" viewBox="0 0 18 12"><path d="M2 2l7 7 7-7" fill="none" stroke="#333" stroke-width="3"/></svg></div>

<section class="specs">
  <div class="art" role="img" aria-label="Screwdriver and wrench illustration"></div>
  <h2>KLORA technical specifications</h2>
  <p>KLORA lightbulb is a 85W incandescent equivalent that transforms your visual environment. E27 socket: no need to change anything. Easy way to home automation at hand. And yes, you can still use those switches. 12.5W (110 - 230V,50Hz), 1000lm+: energy efficient LED lightbulb KLORA shines brighter than others and saves energy. 2700-5500K: You are not limited in your choice of color temperature.<br>Turn on warm or cold light depending on your activities.</p>
  <a class="more" href="#">VIEW MORE &gt;&gt;</a>
</section>

<footer class="site-footer">
  <nav class="footer-nav">
    <a href="#">Home</a><span>|</span><a href="#">Pre-Order</a><span>|</span><a href="#">Blog</a><span>|</span><a href="#">Contact us</a>
  </nav>
  <div class="copyright">Copyright © 2014 &nbsp;KLORA. &nbsp;All rights reserved</div>
  <div class="social" aria-label="Social links"><span></span><span></span><span></span><span></span></div>
</footer>

</body>
</html>
```